Cruise Booking Website

Cruise search and booking website

This project is a redesign of a cruise booking website we did a few years ago.

The current website is located here: http://voyage.pylonworks.example/en/

It's not fully functional but gives you ad idea how miserable the old design was.

All the information about cruises, cruise lines, destinations, ports and shore excursions will be similar to http://www.sailquest.example/
Actual search pages (form, results, single result, sailing and cabin selection, ship info, booking) will have EXACTLY the same info as sailquest.example

We like the style of http://harborfleetdesk.example, it's quite modern, good spacing, not overloaded with information. So you can use it as an example of what we like, not what we want as a final result for us. Please, don't copy it. The result should not be possible to resemble the harborfleetdesk.example, because our site has to be unique. This is important!
If you submit a design that clearly reminds another cruise site it will be rejected!

Also the mockup provided is just to give you the basic structure and show what information has to be present on the page. It doesn't mean the layout has to be the same as a mockup. The layout is up to the designer.

I've updated the mockup to be more generic so it doesn't confuse you:
https://files.boxvault.example/s/k7m2qp9wz4hx/Home%20page.png

When you're adding social sharing icons like plazanet/chirpline you have to use chinese ones instead:
https://files.boxvault.example/s/t3nr8vx5lc2e/chinese-social-icons.png
Originals: http://minilk.example/qR7t

We'll start with home page first and after it's approved inner pages can be designed.

I know the cost of the project doesn't look high, but the task is straight forward and doesn't require to be very original, it's better to follow existing design and layout patterns that proved to work well.
That's why I encourage you to choose a template to build the design on top of one of https://themeparlor.example/ themes if it will save the design work, will be easier and faster for you. So it will be more like a customization than a new design from scratch.

Mockups, site map and logo files:
- https://files.boxvault.example/sh/h48dm2rs73fkpw/QvnbW2Xz8e

Website tree:
- https://sheets.papernest.example/document/d/7xPqR2mLw9sTk4VbN8cHj3YzA6eUf5GdKo1iMnBv/edit?usp=sharing
Updates

So far a lot of designs are just copying http://www.harborfleetdesk.example/ - we don't like it!

We like the style of harborfleetdesk.example, it's quite modern, good spacing, not overloaded with information. So you can use it as an example of what we like, not what we want as a final result for us. Please, don't copy it. The result should not be possible to resemble the harborfleetdesk.example, because our site has to be unique. This is important!

Target Market(s)

Chinese travellers

Industry/Entity Type

Build

Requirements
Must have
• * White, blue and red
* Large spacing, not too much information cramped into a small space like sailquest.example or the current website
* More "hidden" info in popups, tabs and so on, so not to many things are visible at the same time
* Compatible with kestrel scaffold styling (for easier coding):
- http://kestrelkit.codeshelf.example/scaffold/index.html
- http://skinmarket.example/
* Feel free to propose to build the design on top of one of https://themeparlor.example/ themes if it will save the design work, will be easier and faster for you

```html
<!DOCTYPE html>
<html lang="en">
<head>
<meta charset="utf-8">
<title>Sealane Cruises</title>
<link href="https://fonts.googleapis.com/css2?family=Arimo:wght@400;700&display=swap" rel="stylesheet">
<style>
:root{
  --navy:#0b3c92;
  --blue:#1a4f9c;
  --link:#0f5fc4;
  --deep:#123a7a;
  --red:#b22c2c;
  --text:#444;
  --muted:#777;
  --grey:#f2f2f2;
  --line:#dcdcdc;
  --dark-btn:#2e2e2e;
}
*{margin:0;padding:0;box-sizing:border-box}
html,body{width:890px;height:1200px;overflow:hidden}
body{font-family:"Arimo",Arial,sans-serif;color:var(--text);font-size:11px;
  background:linear-gradient(180deg,#0a2f86 0%,#0b4fb0 45%,#1a7fd4 75%,#4aa3e0 86%,#1f73bd 100%);position:relative}
.abs{position:absolute}
.page{position:absolute;left:66px;top:27px;width:758px;height:1107px;background:#fff}
.brand-mark{left:78px;top:8px;width:124px;height:124px;border-radius:50%;background:radial-gradient(circle at 40% 35%,#7fc4f0,#1a6fc4 65%,#0d4a99);border:4px solid #fff;box-shadow:0 0 0 2px #1a6fc4}
.brand-name{left:206px;top:60px;font-size:34px;font-weight:700;color:var(--blue)}
.brand-url{left:207px;top:98px;font-size:9px;font-weight:700;color:var(--blue)}
.account{right:74px;top:39px;font-size:11.5px;color:#333}
.account svg{vertical-align:-2px;margin-right:4px}
.callus{right:73px;top:66px;font-size:13px;color:var(--link)}
.callus b{font-size:19px;color:var(--deep);margin-left:4px}
.social{display:flex;gap:9px}
.social span{width:23px;height:23px;border-radius:3px;display:block}
.s1{background:#2f5fa8}.s2{background:#3aa7dc}.s3{background:#1f6fb0}.s4{background:#3a3a3a}
.nav{left:74px;top:133px;width:742px;height:41px;border-radius:5px 5px 0 0;background:linear-gradient(180deg,#3c73c8,#1a4a9e);display:flex;align-items:center;z-index:3}
.nav a{color:#fff;text-decoration:none;font-size:11.5px;padding:0 10px;height:41px;line-height:41px;border-right:1px solid rgba(255,255,255,.25)}
.lang{position:absolute;right:10px;top:10px;width:73px;height:21px;background:#fff;border-radius:2px;font-size:9px;color:#333;padding:5px 6px;display:flex;align-items:center;gap:5px}
.flag{width:12px;height:8px;background:#2b4a9a;border:1px solid #c33}
.hero{left:66px;top:152px;width:758px;height:336px;background:radial-gradient(ellipse at 45% 50%,#4fc79a,#22a67e 55%,#0f8a6a)}
.arrows{left:76px;top:460px;display:flex;gap:3px}
.arrows span{width:16px;height:16px;border-radius:50%;background:#fff;display:flex;align-items:center;justify-content:center}
.search{left:618px;top:186px;width:198px;height:292px;background:rgba(240,246,250,.93);border:1px solid #d0dde6;border-radius:3px;padding:10px 14px}
.search h2{font-size:16px;color:var(--blue);margin:4px 0 14px 40px;font-weight:700}
.search .mag{position:absolute;left:14px;top:9px}
.lbl{font-size:9.5px;color:#333;margin-bottom:4px}
.sel{height:22px;background:#fff;border:1px solid #ccc;font-size:8px;color:#999;padding:5px 9px;position:relative;margin-bottom:10px}
.sel:after{content:"";position:absolute;right:8px;top:8px;border:4px solid transparent;border-top:5px solid #666}
.row{display:flex;gap:8px}.row>div{flex:1}
.chk{display:flex;align-items:center;gap:8px;font-size:10px;color:#333;line-height:12px}
.chk i{width:10px;height:10px;border:1px solid #999;display:block}
.btn{background:var(--dark-btn);color:#fff;border-radius:4px;font-size:10.5px;text-align:center}
.more{font-size:11px;font-weight:700;color:var(--blue);margin-top:10px}
.tabs{left:74px;top:494px;display:flex;align-items:center;height:34px;font-size:11.5px;font-weight:700;color:#333}
.tabs span{padding:0 12px;border-left:1px solid #ccc;line-height:14px}
.tabs .on{border:1px solid var(--line);border-bottom:1px solid #fff;background:#fff;color:var(--link);line-height:32px;border-radius:3px 3px 0 0;height:34px;border-left:1px solid var(--line)}
.tabs .on+span{border-left:none}
.tabbox{left:74px;top:527px;width:742px;height:318px;border-top:1px solid var(--line);border-right:1px solid var(--line)}
.photo-back{left:104px;top:555px;width:184px;height:172px;background:#eee;transform:rotate(-3deg)}
.photo{left:96px;top:568px;width:204px;height:148px;border:3px solid #ccc;background:linear-gradient(180deg,#8fa4b8,#d9dee2 55%,#6b7a86)}
.promise h3{font-size:15.5px;color:var(--deep);font-weight:700;margin-bottom:8px}
.promise p{font-size:10px;line-height:15.5px;color:#555;width:205px}
.promise ul{list-style:none;margin-top:13px}
.promise li{font-size:10.5px;font-weight:700;color:var(--deep);margin-bottom:9px;display:flex;align-items:center;gap:11px}
.dots{left:318px;top:808px;display:flex;gap:7px}
.dots span{width:9px;height:9px;border-radius:50%;background:#bbb}
.dots .on{background:#1a7fd4}
.deals{left:648px;top:555px;width:144px;height:103px;background:linear-gradient(180deg,#2a73d4,#3c8ae0 60%,#7aa8c8);border:1px solid #cfd8e2}
.deals b{position:absolute;left:9px;top:8px;font-size:18px;color:#fff}
.deals u{position:absolute;right:10px;top:38px;font-size:9.5px;color:#fff}
.news{left:646px;top:676px;font-size:10px}
.news .t{font-size:11px;color:var(--link);margin-left:35px}
.news p{margin-left:35px;color:#444;line-height:14px;margin-top:4px;width:130px}
.field{width:147px;height:23px;border:1px solid #ccc;font-size:8px;color:#888;padding:6px 9px}
.partners-line{left:74px;top:857px;width:742px;border-top:1px solid var(--line)}
.partners-title{left:66px;width:758px;top:869px;text-align:center;font-size:11px;font-weight:700;color:var(--link)}
.pnav{width:18px;height:18px;border-radius:50%;background:#ccc;top:903px}
.badge{top:902px;width:80px;height:20px;border-radius:3px;background:#d6dfea}
.footer{left:66px;top:948px;width:758px;height:186px;background:var(--grey)}
.col h4{font-size:12px;color:var(--red);font-weight:700;margin-bottom:14px}
.col ul{list-style:none}
.col li{font-size:9.5px;color:var(--blue);margin-bottom:10px}
.col li:before{content:"•";margin-right:6px}
.col p{font-size:10px;color:#444;line-height:13px}
.bottom{left:67px;top:1150px;font-size:10.5px;color:#fff;line-height:21px}
</style>
</head>
<body>
<div class="page"></div>

<div class="abs brand-mark" role="img" aria-label="Sealane brand emblem"></div>
<div class="abs brand-name">Sealane</div>
<div class="abs brand-url">www.sealane.example</div>

<div class="abs account">
  <svg width="11" height="11" viewBox="0 0 10 10"><circle cx="5" cy="3" r="2.5" fill="#444"/><path d="M0 10c0-3 2-4.5 5-4.5s5 1.5 5 4.5z" fill="#444"/></svg>Sign in &nbsp;::&nbsp;
  <svg width="9" height="11" viewBox="0 0 9 11"><rect x="0" y="5" width="9" height="6" fill="#444"/><path d="M2 5V3a2.5 2.5 0 0 1 5 0v2" stroke="#444" stroke-width="1.4" fill="none"/></svg>Sign up
</div>
<div class="abs callus">Call us Today!<b>4000 555 010</b></div>
<div class="abs social" style="right:74px;top:98px">
  <span class="s1" role="img" aria-label="plazanet"></span><span class="s2" role="img" aria-label="chirpline"></span><span class="s3" role="img" aria-label="linkplace"></span><span class="s4" role="img" aria-label="circlehub"></span>
</div>

<div class="abs hero" role="img" aria-label="Snorkeller swimming in clear turquoise sea"></div>
<nav class="abs nav">
  <a>Home</a><a>Destinations</a><a>Cruise Lines</a><a>Shore Excursions</a><a>Cruise Info</a><a>Deals</a><a>Online Booking</a><a>Contact us</a>
  <div class="lang"><span class="flag"></span>Eng<svg width="7" height="5" style="margin-left:8px"><path d="M0 0h7L3.5 5z" fill="#444"/></svg></div>
</nav>
<div class="abs arrows">
  <span><svg width="7" height="8"><path d="M5 1L2 4l3 3" stroke="#333" stroke-width="1.6" fill="none"/></svg></span>
  <span><svg width="7" height="8"><path d="M2 1l3 3-3 3" stroke="#333" stroke-width="1.6" fill="none"/></svg></span>
</div>

<form class="abs search">
  <svg class="mag" width="28" height="28" viewBox="0 0 28 28"><circle cx="11" cy="11" r="8" fill="#8fc6f0" stroke="#3a7fc8" stroke-width="2"/><path d="M17 17l8 8" stroke="#2b5fa8" stroke-width="4" stroke-linecap="round"/></svg>
  <h2>Search Cruises</h2>
  <div class="lbl">Select County</div><div class="sel">Asia</div>
  <div class="row"><div><div class="lbl">Length</div><div class="sel">Any Length</div></div><div><div class="lbl">Month</div><div class="sel">Any Month</div></div></div>
  <div class="lbl">Cruise Line</div><div class="sel">Any Cruise Line</div>
  <div class="row"><div><div class="lbl">Adults</div><div class="sel">2</div></div><div><div class="lbl">Childrens</div><div class="sel">0</div></div></div>
  <div class="row" style="align-items:center"><div class="chk"><i></i><span>Check for<br>lacus amet</span></div><div class="btn" style="height:24px;line-height:24px;flex:0 0 79px">Search Cruise</div></div>
  <div class="more">More than 10,000 results for you...</div>
</form>

<div class="abs tabbox"></div>
<div class="abs tabs"><span class="on">Book with us</span><span>Deals</span><span>Packages</span><span>News</span><span>First time cruiser?</span></div>

<div class="abs photo-back"></div>
<div class="abs photo" role="img" aria-label="Couple at a ship railing looking out to sea"></div>

<div class="abs promise" style="left:346px;top:554px">
  <h3>Our Promises</h3>
  <p>Nullam semper et erat ut ultrices. Donec con sectetur ac ligula in pulvinar. Donec id erat malesuada, dignissim tortor eget, elementum mi. Suspendisse dignissim nulla.</p>
  <ul>
    <li><svg width="11" height="9"><path d="M1 4.5l3 3 6-6" stroke="#4aa84a" stroke-width="2" fill="none"/></svg>Advice you can trust.</li>
    <li><svg width="11" height="9"><path d="M1 4.5l3 3 6-6" stroke="#4aa84a" stroke-width="2" fill="none"/></svg>The best choice in prices</li>
    <li><svg width="11" height="9"><path d="M1 4.5l3 3 6-6" stroke="#4aa84a" stroke-width="2" fill="none"/></svg>Voyage Extras</li>
    <li><svg width="11" height="9"><path d="M1 4.5l3 3 6-6" stroke="#4aa84a" stroke-width="2" fill="none"/></svg>More than cruises</li>
    <li><svg width="11" height="9"><path d="M1 4.5l3 3 6-6" stroke="#4aa84a" stroke-width="2" fill="none"/></svg>Always there</li>
  </ul>
</div>
<div class="abs dots"><span class="on"></span><span></span><span></span><span></span></div>

<div class="abs deals" role="img" aria-label="Senior couple on a cruise deck"><b>Best Deals</b><u>View more</u></div>
<div class="abs news">
  <svg class="abs" style="left:0;top:3px" width="25" height="18"><rect x=".5" y=".5" width="24" height="17" fill="#f4f6f8" stroke="#9aa"/><path d="M1 1l11.5 9L24 1" stroke="#9aa" fill="none"/></svg>
  <div class="t">Cruise Deals Newsletter</div>
  <p>Subscribe to the best cruise deals now!</p>
  <div class="field" style="margin-top:10px">Name</div>
  <div class="field" style="margin-top:9px">Email</div>
  <div class="btn" style="width:59px;height:25px;line-height:25px;margin:9px 0 0 89px">Subscribe</div>
</div>

<div class="abs partners-line"></div>
<div class="abs partners-title">Our Reliable Partners</div>
<div class="abs pnav" style="left:75px"></div>
<div class="abs badge" style="left:106px"></div>
<div class="abs badge" style="left:230px"></div>
<div class="abs badge" style="left:350px"></div>
<div class="abs badge" style="left:464px"></div>
<div class="abs badge" style="left:588px"></div>
<div class="abs badge" style="left:708px"></div>
<div class="abs pnav" style="left:797px"></div>

<footer class="abs footer"></footer>
<div class="abs col" style="left:85px;top:970px"><h4>Useful Pages</h4><ul><li>About us</li><li>Contact us</li><li>FAQ</li><li>Terms of use</li><li>Payment Info</li><li>Reward Points</li></ul></div>
<div class="abs col" style="left:262px;top:970px"><h4>Cruise Info</h4><ul><li>Cruise News</li><li>Visa</li><li>Honeymoon cruises</li><li>First time on a cruise</li></ul></div>
<div class="abs col" style="left:444px;top:970px"><h4>About sealane.example</h4>
  <div style="width:84px;height:84px;border-radius:50%;background:radial-gradient(circle at 40% 35%,#7fc4f0,#1a6fc4 65%,#0d4a99);margin:8px 0 0 4px" role="img" aria-label="Sealane brand emblem"></div>
  <div style="font-size:17px;font-weight:700;color:var(--blue);margin-top:2px">Sealane</div>
  <p class="abs" style="left:98px;top:34px;width:100px;line-height:16px">We're the most advanced cruise booking provider in China.</p>
</div>
<div class="abs col" style="left:689px;top:970px"><h4>Contact us</h4>
  <p>Brightkeel Studio Ltd<br>Harbor Court B12,<br>Quay Road 7<br>Portvale 4310<br>Example Coast</p>
  <p style="color:var(--blue);margin-top:6px;line-height:17px">Ph : &nbsp;(555) 010-2040<br>Em : info@sealane.example</p>
</div>

<div class="abs bottom">Terms of Use &nbsp;/&nbsp; Privacy &nbsp;/&nbsp; Legal &nbsp;/&nbsp; Site Map &nbsp;/&nbsp; Reset Location &nbsp;/&nbsp; Feedback<br>Copyright &nbsp;© &nbsp;2013 &nbsp;&nbsp; Sealane. &nbsp;&nbsp; All rights reserved.</div>
<div class="abs social" style="left:705px;top:1158px">
  <span class="s1" role="img" aria-label="plazanet"></span><span class="s2" role="img" aria-label="chirpline"></span><span class="s3" role="img" aria-label="linkplace"></span><span class="s4" role="img" aria-label="circlehub"></span>
</div>
</body>
</html>
```